Business cards in digital learning for freelancer

Hello, I need a business cards in french. I work in the Digital learning industries as freeelancer; I'm an expert in digital learning. I work in France. My customer are in the health industry, pharmaceutical industry, and training organization. I've got a logo. I offer three services: consulting, Design, and Training. In the consulting, I offers coaching to choose your digital learning tools and the digital learning strategy. For the Design, I product differents level of elearning like rapid-learning, elearning, micro-learning, video-learning. And for the training service, I've create training about pedagogy, digital learning management project, Digital learning design.
I join my Logo create in this platform. My universe is gamified. I like the life, and I'm very social. I want a card like I'm I. I love Art (painting), Europeen comics. I use in my visual support "permanent maker" font and caracters. I would like cards: elegant, modern, Top class. If you need any information, you can ask me.
thanks for ideas

Target Market(s)

in health industries and training organization for Training manager, instructor, human resources director

Contact Information for Business Card

Phone number : 06 71 38 95 14 , mail: bastiengolmier@quelmoto.fr, web: bastiengolmier.fr , Carrivo

Font styles to use
Sans Serif

Requirements
Must have
• Use my logo and write my 3 services (consulting, training, design)

```html
<!DOCTYPE html>
<html lang="fr">
<head>
<meta charset="utf-8">
<title>Golmier Digital Learning – Cartes de visite</title>
<link rel="stylesheet" href="https://fonts.googleapis.com/css2?family=Arimo:wght@400;700&family=Cinzel:wght@400&display=swap">
<style>
  :root {
    --bg: #262626;
    --orange: #f37021;
    --white: #ffffff;
    --grey: #7a7a7a;
    --card-w: 760px;
    --card-h: 420px;
  }
  * { margin: 0; padding: 0; box-sizing: border-box; }
  html, body { width: 1200px; height: 1015px; overflow: hidden; background: var(--bg); }
  .sheet {
    position: relative; width: 1200px; height: 1015px;
    font-family: "Arimo", Arial, sans-serif; color: var(--white);
  }
  .card {
    position: absolute; width: var(--card-w); height: var(--card-h);
    overflow: hidden; box-shadow: 0 14px 30px rgba(0,0,0,.55);
  }
  .card--back { left: 150px; top: 58px; }
  .card--front { left: 290px; top: 537px; }
  .card__shape { position: absolute; inset: 0; width: 100%; height: 100%; display: block; }

  .brand {
    position: absolute; left: 440px; top: 105px; width: 280px;
    color: var(--orange); font-weight: 700; text-align: center;
    font-size: 30px; line-height: 1.15; letter-spacing: 1px; text-transform: uppercase;
  }
  .brand__dot {
    display: block; width: 64px; height: 64px; margin: 0 auto 14px;
    border-radius: 50%; background: var(--orange);
  }

  .services { position: absolute; left: 78px; top: 150px; list-style: none; }
  .services li {
    font-size: 18px; letter-spacing: 1.5px; text-transform: uppercase; line-height: 32px;
    display: flex; align-items: center; gap: 10px;
  }
  .services li::before {
    content: ""; width: 8px; height: 8px; border-radius: 50%; background: var(--white);
  }
  .rule { position: absolute; left: 78px; height: 1px; background: rgba(255,255,255,.55); }
  .rule--services { top: 262px; width: 230px; }
  .rule--social { top: 322px; width: 280px; }
  .social {
    position: absolute; left: 160px; top: 307px;
    display: flex; align-items: center; gap: 8px;
    background: var(--orange); padding: 0 10px;
    font-size: 15px; font-weight: 700;
  }
  .social__dot { width: 30px; height: 30px; border-radius: 50%; background: var(--white); }

  .person { position: absolute; left: 70px; top: 150px; }
  .person__name { font-family: "Cinzel", Georgia, serif; font-size: 25px; letter-spacing: 0.5px; line-height: 1.1; white-space: nowrap; }
  .person__role { font-size: 19px; margin-top: 4px; }
  .contact { position: absolute; left: 70px; top: 265px; list-style: none; }
  .contact li { display: flex; align-items: center; gap: 10px; font-size: 17px; line-height: 30px; white-space: nowrap; }
  .contact svg { width: 18px; height: 18px; fill: none; stroke: var(--white); stroke-width: 1.8; }
</style>
</head>
<body>
<main class="sheet">

  <section class="card card--back" aria-label="Verso de la carte">
    <svg class="card__shape" viewBox="0 0 760 420" aria-hidden="true">
      <rect width="760" height="420" fill="var(--orange)"/>
      <circle cx="565" cy="178" r="196" fill="var(--white)"/>
      <circle cx="578" cy="170" r="192" fill="var(--grey)"/>
      <circle cx="582" cy="170" r="190" fill="var(--white)"/>
      <polygon points="582,0 760,0 760,330 582,360" fill="var(--white)"/>
    </svg>
    <ul class="services">
      <li>Consulting</li>
      <li>Training</li>
      <li>Design</li>
    </ul>
    <div class="rule rule--services"></div>
    <div class="rule rule--social"></div>
    <div class="social"><span class="social__dot"></span>Carrivo</div>
    <div class="brand"><span class="brand__dot"></span>Golmier Digital Learning</div>
  </section>

  <section class="card card--front" aria-label="Recto de la carte">
    <svg class="card__shape" viewBox="0 0 760 420" aria-hidden="true">
      <rect width="760" height="420" fill="var(--orange)"/>
      <circle cx="565" cy="178" r="196" fill="var(--white)"/>
      <circle cx="578" cy="170" r="192" fill="var(--grey)"/>
      <circle cx="582" cy="170" r="190" fill="var(--white)"/>
      <polygon points="582,0 760,0 760,330 582,360" fill="var(--white)"/>
    </svg>
    <div class="person">
      <p class="person__name">Julien Marchand</p>
      <p class="person__role">Managing Director</p>
    </div>
    <ul class="contact">
      <li>
        <svg viewBox="0 0 24 24" aria-hidden="true"><path d="M5 3h4l2 5-2.5 1.5a11 11 0 0 0 6 6L16 13l5 2v4a2 2 0 0 1-2 2A17 17 0 0 1 3 5a2 2 0 0 1 2-2z"/></svg>
        06 71 38 95 14
      </li>
      <li>
        <svg viewBox="0 0 24 24" aria-hidden="true"><rect x="2" y="5" width="20" height="14"/><path d="M2 5l10 8 10-8"/></svg>
        bastiengolmier@quelmoto.fr
      </li>
      <li>
        <svg viewBox="0 0 24 24" aria-hidden="true"><circle cx="12" cy="12" r="10"/><path d="M2 12h20M12 2c3 3 3 17 0 20M12 2c-3 3-3 17 0 20"/></svg>
        www.bastiengolmier.fr
      </li>
    </ul>
    <div class="brand"><span class="brand__dot"></span>Golmier Digital Learning</div>
  </section>

</main>
</body>
</html>
```